New Business Card for our Indoor Golf Training Facility

We are looking for designs for a new business card for our indoor golf training facility. Attached is our logo, our logo with our slogan, and here is our elevator pitch (What makes us different from the others) not sure if all the info will fit on one card, maybe you can condense the elevator pitch? here is the info

Elevator Pitch
We work with serious golfers and those that want to be serious golfers…
to make you better, faster, at all phases of the game…
We use the same state-of-the-art technology as professional golfers…
which produces data sets that shows your improvement in real time.
Our facility is available 24/7 to our members, which allows you to improve on your time.

our website: www.birchpinlinks.com

Target Market(s)

Golfers

Font styles to use
Serif
Sans Serif

Colors
ec1f27
f59195
fbd4d5
919191
d3d3d3
1b1b1b

Requirements
Must have
• our logo or our logo with the slogan, elevator pitch (can be condensed or shortened)

```html
<!DOCTYPE html>
<html lang="en">
<head>
<meta charset="utf-8">
<title>Birchpin Links – Business Card</title>
<link rel="stylesheet" href="https://fonts.googleapis.com/css2?family=Roboto:ital,wght@0,300;0,400;0,700;0,900;1,400&family=Roboto+Condensed:ital,wght@0,400;0,700;1,400&display=swap">
<style>
  :root {
    --red: #ec1f27;
    --pink: #f59195;
    --blush: #fbd4d5;
    --grey: #919191;
    --grey-light: #d3d3d3;
    --ink: #1b1b1b;
    --white: #ffffff;
    --stage: #ececec;
  }
  * { box-sizing: border-box; margin: 0; padding: 0; }
  html, body { width: 1200px; height: 911px; overflow: hidden; }
  body {
    background: var(--stage);
    font-family: "Roboto", Arial, sans-serif;
    position: relative;
  }
  .card {
    position: absolute;
    width: 540px;
    height: 309px;
    border-radius: 18px;
    overflow: hidden;
    box-shadow: 0 6px 18px rgba(0,0,0,.18);
  }
  /* Front */
  .card--front { left: 30px; top: 301px; background: var(--white); }
  .contact-panel {
    position: absolute;
    left: 282px; top: 0;
    width: 228px; height: 196px;
    background: var(--red);
    border-radius: 0 0 16px 16px;
    color: var(--white);
    padding: 30px 20px 0 22px;
  }
  .contact-name { font-weight: 700; font-size: 22px; line-height: 1.1; }
  .contact-title { font-size: 13px; font-weight: 400; margin-top: 3px; }
  .contact-address { font-size: 11.5px; line-height: 1.45; margin-top: 12px; }
  .contact-list { list-style: none; margin-top: 10px; font-size: 11.5px; line-height: 1.55; }
  .contact-list li { display: flex; align-items: center; gap: 7px; }
  .contact-list svg { width: 10px; height: 10px; flex: none; }
  .brand { position: absolute; }
  .brand-name { font-weight: 900; line-height: 1; letter-spacing: -.3px; }
  .brand-slogan { font-weight: 400; letter-spacing: .2px; margin-top: 4px; }
  .card--front .brand { left: 34px; top: 218px; color: var(--red); }
  .card--front .brand-name { font-size: 30px; }
  .card--front .brand-slogan { font-size: 11px; }

  /* Back */
  .card--back {
    left: 630px; top: 301px;
    background: var(--red);
    color: var(--white);
    text-align: center;
  }
  .card--back .brand { left: 0; right: 0; top: 30px; }
  .card--back .brand-name { font-size: 38px; }
  .card--back .brand-slogan { font-size: 13px; font-weight: 300; }
  .pitch { position: absolute; left: 24px; right: 24px; top: 124px; }
  .pitch-heading {
    font-family: "Roboto Condensed", "Arial Narrow", sans-serif;
    font-weight: 700; font-size: 17px; letter-spacing: .5px;
  }
  .pitch-text {
    font-family: "Roboto Condensed", "Arial Narrow", sans-serif;
    font-style: italic; font-size: 12.5px; line-height: 1.5; margin-top: 8px;
  }
</style>
</head>
<body>
  <section class="card card--front" aria-label="Business card front">
    <div class="brand">
      <div class="brand-name">Birchpin Links</div>
      <div class="brand-slogan">Train Smart. Play Sharp. Every Day.</div>
    </div>
    <div class="contact-panel">
      <h1 class="contact-name">Daniel Reeve</h1>
      <p class="contact-title">CEO/Founder</p>
      <p class="contact-address">1480 W. Alder Rd, Unit B4<br>Fairview, OH 45102</p>
      <ul class="contact-list">
        <li><svg viewBox="0 0 10 10" aria-hidden="true"><path fill="#fff" d="M2 0.5l2 2-1 1.2c.6 1.3 1.5 2.2 2.8 2.8L7 5.5l2 2L8 9.5C4.2 9.3.7 5.8.5 2z"/></svg>555-201-7730</li>
        <li><svg viewBox="0 0 10 10" aria-hidden="true"><rect x=".5" y="2" width="9" height="6.5" rx="1" fill="#fff"/><path d="M1 2.5l4 3 4-3" stroke="#ec1f27" fill="none"/></svg>info@birchpinlinks.com</li>
        <li><svg viewBox="0 0 10 10" aria-hidden="true"><circle cx="5" cy="5" r="4.3" fill="none" stroke="#fff" stroke-width="1.2"/><path d="M.8 5h8.4M5 .8c-2 2.5-2 5.9 0 8.4M5 .8c2 2.5 2 5.9 0 8.4" stroke="#fff" fill="none" stroke-width=".8"/></svg>www.birchpinlinks.com</li>
      </ul>
    </div>
  </section>

  <section class="card card--back" aria-label="Business card back">
    <div class="brand">
      <div class="brand-name">Birchpin Links</div>
      <div class="brand-slogan">Train Smart. Play Sharp. Every Day.</div>
    </div>
    <div class="pitch">
      <h2 class="pitch-heading">ELEVATOR PITCH:</h2>
      <p class="pitch-text">
        We work with serious golfers and those that want to be serious golfers…<br>
        to make you better, faster, at all phases of the game…<br>
        We use the same state-of-the-art technology as professional golfers…<br>
        which produces data sets that shows your improvement in real time.<br>
        Our facility is available 24/7 to our members, which allows you to improve on your time.
      </p>
    </div>
  </section>
</body>
</html>
```